Kesso Tea Premium Matcha brand Label

This is a label design project for a luxury tea brand. Feel free to be creative within the guidelines.
Attached to this project is a document called “Private Label Design Requirements” with the design guidelines and template. There is another document called "Kesso Tea Packaging Instructions" this has more details necessary to stick to the guidelines in the first document.

I have also attached the certifications to be included as well as different variations of the logo for you to use.

If you have any questions, I am here.
Updates

Need extra days to review

Target Market(s)

Young, active, fun, enjoy the finer things

```html
<!DOCTYPE html>
<html lang="en">
<head>
<meta charset="utf-8">
<title>Kesso Tea Premium Organic Ceremonial Matcha Label</title>
<link href="https://fonts.googleapis.com/css2?family=Montserrat:wght@500;600;700;800&display=swap" rel="stylesheet">
<style>
  :root {
    --bg: #8e8f93;
    --label: #f1f1f1;
    --ink: #1e1e1e;
    --ink-soft: #3a3a3a;
    --matcha: #5fa94b;
    --bracket: #4a4a4a;
    --badge-green: #6aa84f;
    --badge-blue: #3e6fb0;
  }
  * { box-sizing: border-box; margin: 0; padding: 0; }
  html, body { width: 1200px; height: 430px; overflow: hidden; }
  body {
    background: var(--bg);
    font-family: "Montserrat", sans-serif;
    color: var(--ink);
    display: flex;
    align-items: center;
    justify-content: center;
  }
  .label {
    width: 1140px;
    height: 300px;
    background: var(--label);
    border-radius: 6px;
    display: grid;
    grid-template-columns: 1fr 1.25fr 1fr;
  }
  .panel { position: relative; }

  /* left side panel */
  .panel--origin {
    display: flex;
    align-items: center;
    justify-content: center;
    padding-top: 40px;
  }
  .origin-text { font-size: 12.5px; font-weight: 600; line-height: 1.25; color: var(--ink-soft); }
  .origin-text .cert { margin-top: 8px; }

  /* front panel */
  .panel--front {
    display: flex;
    flex-direction: column;
    align-items: center;
    justify-content: center;
    padding-top: 20px;
  }
  .brand {
    display: flex;
    align-items: center;
    gap: 7px;
    font-size: 15px;
    font-weight: 700;
    color: var(--ink);
    margin-bottom: 14px;
  }
  .brand-dot { width: 12px; height: 12px; border-radius: 50%; background: var(--matcha); }
  .product-title {
    position: relative;
    font-size: 33px;
    font-weight: 800;
    line-height: 1.05;
    text-align: center;
    letter-spacing: 0.5px;
    padding: 0 46px;
  }
  .product-title::before,
  .product-title::after {
    content: "";
    position: absolute;
    top: 2px;
    bottom: 6px;
    width: 38px;
    border: 3px solid var(--bracket);
  }
  .product-title::before { left: -4px; border-right: none; }
  .product-title::after { right: -4px; border-left: none; }
  .product-title .accent { color: var(--matcha); }
  .net-weight { margin-top: 14px; font-size: 16px; font-weight: 600; letter-spacing: 0.5px; }

  /* right side panel */
  .panel--info {
    display: flex;
    flex-direction: column;
    justify-content: center;
    padding: 40px 0 0 36px;
  }
  .info-heading { font-size: 14px; font-weight: 700; margin-bottom: 2px; }
  .info-line { font-size: 10px; font-weight: 600; line-height: 1.35; }
  .info-list { list-style: none; margin-bottom: 12px; }
  .info-list li::before { content: "\2022 "; }
  .ingredients { margin-bottom: 8px; }
  .cert-row { display: flex; align-items: center; gap: 8px; }
  .badge-square { width: 22px; height: 22px; background: var(--badge-blue); border: 3px solid var(--badge-green); }
  .badge-circle { width: 26px; height: 26px; border-radius: 50%; border: 3px solid var(--badge-green); background: #fff; }
  .storage { margin-left: 6px; font-size: 10px; font-weight: 700; line-height: 1.2; }
</style>
</head>
<body>
  <main class="label">
    <section class="panel panel--origin">
      <div class="origin-text">
        <p>Product of Japan</p>
        <p>Distributed by:</p>
        <p>Kesso Tea Co. | Cedar Vale, Ga</p>
        <p class="cert">Certified Organic by orvel</p>
      </div>
    </section>

    <section class="panel panel--front">
      <div class="brand"><span class="brand-dot"></span>Kesso Tea</div>
      <h1 class="product-title">PREMIUM ORGANIC<br>CEREMONIAL <span class="accent">MATCHA</span></h1>
      <p class="net-weight">Net Wt: 30g</p>
    </section>

    <section class="panel panel--info">
      <div class="ingredients">
        <h2 class="info-heading">Ingredients:</h2>
        <p class="info-line">Premium Organic Japanese Matcha Green Tea</p>
      </div>
      <h2 class="info-heading">Instructions:</h2>
      <ul class="info-list info-line">
        <li>2 tsp of Matcha</li>
        <li>2oz of Water (170-180 degrees F)</li>
        <li>Whisk in a W formation until frothy</li>
        <li>Sweeten to taste</li>
      </ul>
      <div class="cert-row">
        <span class="badge-square" role="img" aria-label="Non-GMO verification badge"></span>
        <span class="badge-circle" role="img" aria-label="Organic certification seal"></span>
        <p class="storage">KEEP REFRIGERATED<br>FOR QUALITY</p>
      </div>
    </section>
  </main>
</body>
</html>
```